Gutschein-Design für Verkauf von Online-Schmuckstücken
Zielgruppe
Wir verkaufen Online Schmuckstücke!
www.silberfaden-shop.de
Aufgabenstellung
Wir haben eine schwarze Schachtel erstellt und da drinne wird eine Geschenkgutschein sein:
Es soll sehr schlicht sein und schwarzen Hintergrund haben.
Vorderseite nur unser LOGO.
Rückseite:
Betrag: _________
Gültig Bis: _________
Code: __________
Und unten klein gedruckt steht:
Diese Karte ist gültig nur auf der online shop seite www.silberfaden-shop.de und in unserer offizielen Stores. Dieses Karte ist nicht gültig bei rabatierte Produkten und man kann nicht mit dieser karte einen Gutscheinkarte kaufen.
Der Design soll sehr schlicht und dezenz sein.

```html
<!DOCTYPE html>
<html lang="de">
<head>
<meta charset="utf-8">
<title>Silberfaden – Geschenkgutschein</title>
<link rel="stylesheet" href="https://fonts.googleapis.com/css2?family=Great+Vibes&family=Montserrat:wght@400&display=swap">
<style>
  :root {
    --backdrop: #efeeeb;
    --card: #1d1b18;
    --card-edge: #2a2824;
    --gold: #d6ae45;
    --ink-light: #f2efe8;
    --rule: #cfcac0;
  }
  * { box-sizing: border-box; margin: 0; padding: 0; }
  html, body {
    width: 1200px;
    height: 898px;
    overflow: hidden;
    background: var(--backdrop);
  }
  .sheet {
    position: relative;
    width: 1200px;
    height: 898px;
  }
  .voucher {
    position: absolute;
    left: 200px;
    width: 800px;
    height: 380px;
    background: var(--card);
    box-shadow: 0 0 0 1px var(--card-edge), 0 6px 18px rgba(0,0,0,.18);
  }
  .voucher--front { top: 59px; }
  .voucher--back  { top: 459px; }

  /* Front: brand mark */
  .brand {
    position: absolute;
    inset: 0;
    display: flex;
    flex-direction: column;
    align-items: center;
    justify-content: center;
    gap: 22px;
  }
  .brand__disc {
    width: 170px;
    height: 170px;
    border-radius: 50%;
    background: var(--gold);
  }
  .brand__name {
    font-family: "Great Vibes", cursive;
    font-size: 54px;
    line-height: 1;
    color: var(--gold);
  }

  /* Back: fields */
  .field {
    position: absolute;
    display: flex;
    align-items: flex-end;
    color: var(--ink-light);
    font-family: "Great Vibes", cursive;
  }
  .field__label {
    text-align: right;
    line-height: 1;
  }
  .field__line {
    position: absolute;
    left: 344px;
    width: 250px;
    height: 1px;
    background: var(--rule);
  }
  .field--amount { left: 0; top: 70px; }
  .field--amount .field__label { width: 316px; font-size: 44px; }
  .field--amount .field__line { top: 48px; }

  .field--valid { left: 0; top: 162px; }
  .field--valid .field__label { width: 316px; font-size: 32px; }
  .field--valid .field__line { top: 34px; }

  .field--code { left: 0; top: 218px; }
  .field--code .field__label { width: 316px; font-size: 32px; }
  .field--code .field__line { top: 34px; }

  .fineprint {
    position: absolute;
    left: 0;
    right: 0;
    bottom: 22px;
    text-align: center;
    font-family: "Montserrat", sans-serif;
    font-size: 9.5px;
    line-height: 1.55;
    color: var(--ink-light);
  }
</style>
</head>
<body>
<main class="sheet">
  <section class="voucher voucher--front" aria-label="Gutschein Vorderseite">
    <div class="brand">
      <div class="brand__disc"></div>
      <div class="brand__name">Silberfaden</div>
    </div>
  </section>

  <section class="voucher voucher--back" aria-label="Gutschein Rückseite">
    <div class="field field--amount">
      <span class="field__label">Betrag:</span>
      <span class="field__line"></span>
    </div>
    <div class="field field--valid">
      <span class="field__label">Gültig bis:</span>
      <span class="field__line"></span>
    </div>
    <div class="field field--code">
      <span class="field__label">Code:</span>
      <span class="field__line"></span>
    </div>
    <p class="fineprint">
      Diese Karte ist nur gültig auf der Online Shop Seite www.silberfaden-shop.de und in unseren offiziellen Stores.<br>
      Diese Karte ist nicht gültig bei bereits reduzierten Produkten und kann nicht zum Kauf eines Gutscheins verwendet werden.
    </p>
  </section>
</main>
</body>
</html>
```